Stylish Business Cards Wanted

- DOUBLE SIDED Design Required -

High end, edgy cards for a corporate and personal stylist. Must include logo,
Name: Belinda Harwick
Title: Director and Stylist
telephone : +61 8 7142 5809
email: belinda@theloombriefing.example
website: theloombriefing.example
Tag: Corporate Workwear & Uniform Specialist | Personal Stylist
Would like nice icons for telephone, email, website

Target Market(s)

Businesses wanting stylish uniforms, people wanting stylish wardrobes

Industry/Entity Type

Corporate Workwear Stylist

Contact Information for Business Card

I would like black, white and gold foiling incorporated in the design - possibly a touch of the other colours on my branding guide attached Name: Belinda Harwick Title: Director and Stylist telephone : +61 8 7142 5809 email: belinda@theloombriefing.example website: theloombriefing.example Tag: Corporate Workwear & Uniform Specialist | Personal Stylist Would like nice icons for telephone, email, website

Font styles to use
Other font styles liked:
• Raleway

Colors

Designer to choose colors to be used in the design.

Requirements
Must have
• Gold foil accents

```html
<!DOCTYPE html>
<html lang="en">
<head>
<meta charset="utf-8">
<title>The Loom Briefing — Business Cards</title>
<link rel="stylesheet" href="https://fonts.googleapis.com/css2?family=Montserrat:wght@400;500;600&family=Raleway:wght@400;500&display=swap">
<style>
  :root {
    --backdrop: #e2e2e2;
    --ink: #0c0c0c;
    --paper: #ffffff;
    --gold: #e3b53c;
    --gold-pale: #f1dc9f;
    --text: #1e1e1e;
    --fold: #ececec;
  }
  * { box-sizing: border-box; margin: 0; padding: 0; }
  html, body {
    width: 1200px; height: 900px; overflow: hidden;
    background: var(--backdrop);
    font-family: "Montserrat", Arial, sans-serif;
  }
  .sheet {
    position: relative; width: 1200px; height: 900px;
    display: flex; flex-direction: column; align-items: center;
    justify-content: center; gap: 44px;
  }
  .card {
    position: relative; width: 640px; height: 370px;
    box-shadow: 0 6px 18px rgba(0,0,0,0.18);
    overflow: hidden;
  }

  /* Front */
  .card--front { background: var(--ink); }
  .front-pattern {
    position: absolute; inset: 0 0 96px 0;
    background: linear-gradient(115deg, #101111 0%, #1f2121 45%, #0d0e0e 70%, #1a1b1b 100%);
  }
  .front-brand {
    position: absolute; top: 56px; right: 64px;
    display: flex; align-items: center; gap: 10px;
    color: var(--gold); font-weight: 600; font-size: 20px; letter-spacing: 1px;
    white-space: nowrap;
  }
  .front-brand .dot { width: 10px; height: 10px; border-radius: 50%; background: var(--gold); }
  .tag-band {
    position: absolute; left: 0; right: 0; bottom: 34px; height: 62px;
    padding: 0 32px;
    border-top: 2px solid var(--gold); border-bottom: 2px solid var(--gold);
    display: flex; align-items: center; justify-content: center; gap: 12px;
    color: var(--gold); font-weight: 500; font-size: 15px; letter-spacing: 0.4px;
    white-space: nowrap; background: var(--ink);
  }
  .tag-band .sep { color: var(--paper); font-weight: 400; }

  /* Back */
  .card--back { background: var(--paper); display: flex; }
  .back-brand {
    width: 44%; padding: 0 24px;
    display: flex; align-items: center; justify-content: center;
    border-right: 1px solid var(--fold);
  }
  .brand-name {
    display: flex; align-items: center; gap: 10px;
    font-weight: 600; font-size: 22px; color: var(--ink); letter-spacing: 0.4px;
    white-space: nowrap;
  }
  .brand-name .square { flex: none; width: 12px; height: 12px; background: var(--ink); }
  .back-contact { flex: 1; padding: 58px 34px 0 30px; }
  .person { position: relative; padding-bottom: 4px; }
  .person-name { font-weight: 500; font-size: 24px; color: var(--text); white-space: nowrap; }
  .person-title { font-family: "Raleway", Arial, sans-serif; font-size: 14px; color: var(--gold); margin-top: 2px; }
  .person::after {
    content: ""; position: absolute; left: 220px; right: 0; top: 14px;
    height: 1px; background: var(--gold-pale);
  }
  .contact-list { list-style: none; margin-top: 66px; }
  .contact-item {
    display: flex; align-items: center; gap: 16px;
    padding: 7px 0; border-bottom: 1px solid var(--gold-pale);
    font-family: Arial, Helvetica, sans-serif; font-size: 15px; color: var(--text);
    white-space: nowrap;
  }
  .contact-icon {
    flex: none; width: 22px; height: 22px; border-radius: 50%;
    background: var(--ink); display: flex; align-items: center; justify-content: center;
  }
  .contact-icon svg { width: 12px; height: 12px; }
</style>
</head>
<body>
<main class="sheet">
  <section class="card card--front" aria-label="Business card front">
    <div class="front-pattern" role="img" aria-label="Repeating brand wordmark pattern in soft charcoal on black"></div>
    <div class="front-brand"><span class="dot"></span>The Loom Briefing</div>
    <div class="tag-band">
      <span>CORPORATE WORKWEAR</span><span class="sep">|</span>
      <span>UNIFORM SPECIALIST</span><span class="sep">|</span>
      <span>PERSONAL STYLIST</span>
    </div>
  </section>

  <section class="card card--back" aria-label="Business card back">
    <div class="back-brand">
      <div class="brand-name"><span class="square"></span>The Loom Briefing</div>
    </div>
    <div class="back-contact">
      <div class="person">
        <h1 class="person-name">Belinda Harwick</h1>
        <p class="person-title">Director and Stylist</p>
      </div>
      <ul class="contact-list">
        <li class="contact-item">
          <span class="contact-icon"><svg viewBox="0 0 24 24"><path fill="#e3b53c" d="M6.6 10.8a15.1 15.1 0 0 0 6.6 6.6l2.2-2.2c.3-.3.7-.4 1-.2 1.1.4 2.3.6 3.6.6.6 0 1 .4 1 1V20c0 .6-.4 1-1 1A17 17 0 0 1 3 4c0-.6.4-1 1-1h3.5c.6 0 1 .4 1 1 0 1.3.2 2.5.6 3.6.1.3 0 .7-.2 1z"/></svg></span>
          +61 8 7142 5809
        </li>
        <li class="contact-item">
          <span class="contact-icon"><svg viewBox="0 0 24 24"><rect x="2" y="5" width="20" height="14" rx="1.5" fill="#e3b53c"/><path d="M3 6l9 7 9-7" fill="none" stroke="#0c0c0c" stroke-width="1.6"/></svg></span>
          belinda@theloombriefing.example
        </li>
        <li class="contact-item">
          <span class="contact-icon"><svg viewBox="0 0 24 24"><g fill="none" stroke="#e3b53c" stroke-width="2"><circle cx="12" cy="12" r="9"/><path d="M3 12h18M12 3c3 3 3 15 0 18M12 3c-3 3-3 15 0 18"/></g></svg></span>
          www.theloombriefing.example
        </li>
      </ul>
    </div>
  </section>
</main>
</body>
</html>
```